Shopfront Graphics , front,side doors, small wall and mall entry.

New graphics retail store opening.

We are looking for a contemporary store front graphic that screams, Graphics, colour and ATTENTION.

The Fascia is approximately 3m high x 5 metres wide. We envisage a lightbox along the top and graphics continuing across the glass below.

We then have the side wall and graphics approximately 2.5m x 10m, and then second floor with glass and concrete.

Can we try a theme that partially covers all walls ..window frames and glass...Not overdone, but similar to the area covered in my demo pic of another store...Not just limited to the paint splash...your ideas...concepts?

Just to save all graphicos time at the initial concept stage,

Can we just stick to the front signage and the successful designer can just continue theme on other windows..
ORRRRRR..if you really want to impress and you have time....as before do the lot!
Just looking for the THEME layout at first.

Thanks
TM

Please see new front windows...do not follow this designers image, please ignore. But please note the front door now on Right hand side of front. 

We do have an interesting angle now, I would like minimal graphics now. Velmoria on light box above glass...but do need some theme.

I will place on here some more printed samples from our logo.

Note we need the TV screens to be seen  but some nice pattern/design to hold all the windows together!!

Thanks Tobias

OK we seem to be going the wrong way with splashes now..Too much and starting to look TOO colourful and TOO messy...I have attached some images that I took off Pixmorrow that are more in keeping with what I am looking for. I will also send you a rough sketch of an interior plan or "LOOK". 

The inside of the store is being professionally designed..White on white.. I am thinking of introducing one vibrant stripe.
Hope this helps with the "FEEL".....

Target Market(s)

This shop is a high street location with a lot of pedestrians.
The store is being designed as a fun collaborative store with seating and computer stations where anyone can come in and design, Photobooks, full colour T shirts, posters, Photogifts such as Mugs, Mouse mats, Canvas fine art pictures....

General atmosphere is FUN, entertaing and based on consumers wandering in, a bit like the ZENDRIL HALL experience.

We also make commercial signage, vehicle wraps, acrylic signs, photocopy and print banners. Regular signshop products.

Industry/Entity Type

Retail

Font styles to use
Sans Serif

Colors
9bcb3b
e34197
33a6d7

Requirements
Must have
• Our logo.
Lets concentrate on the main front window and light box with logo....see new updated files.
Velmoria, as designed by quillvane guys!!
Nice to have
• THe walls and windows should have a theme pattern, like the attached sign shop. I like that look with the full colour splash but we are very open to your ideas.
Should not have
• Pictures of CATS!

```html
<!DOCTYPE html>
<html lang="en">
<head>
<meta charset="utf-8">
<title>Velmoria – Shopfront Lightbox</title>
<link rel="stylesheet" href="https://fonts.googleapis.com/css2?family=Montserrat:wght@800&display=swap">
<style>
  :root {
    --bg-edge: #1c1c1c;
    --bg-mid: #2a2a2b;
    --bg-glow: #3d3d3e;
    --frame: #0d0d0d;
    --wordmark: #c4c4c6;
    --lime: #9bcb3b;
    --magenta: #e34197;
    --sky: #33a6d7;
    --orange: #f7941d;
    --yellow: #ffcb05;
    --teal: #1fb5b0;
    --violet: #3c3d96;
    --purple: #9b2c8f;
    --indigo: #5b6fc4;
  }
  html, body {
    margin: 0;
    padding: 0;
    width: 1200px;
    height: 722px;
    overflow: hidden;
    background: var(--bg-edge);
  }
  .lightbox {
    position: relative;
    width: 1200px;
    height: 722px;
    box-sizing: border-box;
    border: 1px solid var(--frame);
    overflow: hidden;
    background: radial-gradient(ellipse 520px 380px at 600px 330px, var(--bg-glow) 0%, var(--bg-mid) 55%, var(--bg-edge) 100%);
  }
  .splash {
    position: absolute;
    opacity: 0.95;
  }
  .splash--top-left {
    left: 0; top: 0;
    width: 480px; height: 140px;
    border-radius: 0 0 70% 20% / 0 0 100% 60%;
    background: linear-gradient(100deg, var(--lime) 0%, var(--orange) 30%, var(--teal) 62%, var(--yellow) 85%);
  }
  .splash--top-right {
    right: 0; top: 0;
    width: 330px; height: 290px;
    border-radius: 0 0 0 70% / 0 0 0 80%;
    background: linear-gradient(110deg, var(--violet) 0%, #6a2f96 45%, var(--purple) 100%);
  }
  .splash--bottom-left {
    left: 0; bottom: 0;
    width: 330px; height: 215px;
    border-radius: 0 60% 0 0 / 0 70% 0 0;
    background: linear-gradient(70deg, var(--indigo) 0%, #3f8fd8 55%, var(--sky) 100%);
  }
  .splash--bottom-right {
    right: 0; bottom: 32px;
    width: 530px; height: 175px;
    border-radius: 60% 0 0 60% / 50% 0 0 70%;
    background: linear-gradient(95deg, var(--lime) 0%, #c9b92a 40%, var(--orange) 72%, var(--teal) 100%);
  }
  .brand {
    position: absolute;
    left: 300px;
    top: 349px;
    display: flex;
    align-items: flex-start;
    gap: 16px;
  }
  .brand__mark {
    width: 76px;
    height: 76px;
    margin-top: 8px;
    background: var(--lime);
  }
  .brand__name {
    margin: 0;
    font-family: "Montserrat", Arial, sans-serif;
    font-weight: 800;
    font-size: 108px;
    line-height: 1;
    letter-spacing: -3px;
    color: var(--wordmark);
    white-space: nowrap;
  }
</style>
</head>
<body>
  <main class="lightbox">
    <div class="splash splash--top-left" role="img" aria-label="Flowing paint ribbon in lime, orange, teal and yellow"></div>
    <div class="splash splash--top-right" role="img" aria-label="Purple and violet paint splash"></div>
    <div class="splash splash--bottom-left" role="img" aria-label="Blue paint splash"></div>
    <div class="splash splash--bottom-right" role="img" aria-label="Flowing paint ribbon in lime, orange and teal"></div>
    <div class="brand">
      <span class="brand__mark" aria-hidden="true"></span>
      <h1 class="brand__name">Velmoria</h1>
    </div>
  </main>
</body>
</html>
```